Design the Business card for NetVaultic

Business card required for a professional Cyber Security business.
Company Logo and Icon has already been provided however I would like other options for the logo and icon to compare to. Alternatively, please refine/enhance the image of the logo.icon I have already provided.

If you are going to use the provided logo and icon, I was thinking that the company raised Logo on White background would serve well on the front of the card. See attached. AND, a large company raised stand-alone icon to appear on black background on the back of the card with tagline 'Cyber Risk Management, Governance and Consulting' or 'Cyber Security for your Business' See attached.
Alternatively, provide your own design for the logo and icon.

Target Market(s)

Enterprise, Government, Financial.

Contact Information for Business Card

Tavin Orloweth
Founder and CEO

Email Address
Mobile Number
Website URL
LinkedIn URL

Logo Text

NetVaultic - see attached example of logo

Font styles to use
Other font styles liked:
• Berlin Sans FB

Requirements
Must have
• Clean large and bold icon on the back with tagline.
• Horizontal alignment,
Nice to have
• Round edges.
• Raised Logo/Icon
Should not have
• An unprofessional look and feel.

```html
<!DOCTYPE html>
<html lang="en">
<head>
<meta charset="utf-8">
<title>NetVaultic Business Card</title>
<link rel="stylesheet" href="https://fonts.googleapis.com/css2?family=Roboto:wght@400&family=Roboto+Condensed:wght@500&family=Ubuntu:wght@500&display=swap">
<style>
  :root {
    --stage: #e8e5e0;
    --card-front: #f7f7f7;
    --card-back: #1a1c1f;
    --brand-blue: #1b6fc4;
    --tagline-blue: #3f78c9;
    --brand-yellow: #f6b800;
    --rule: #8d8d8d;
    --ink: #444;
    --icon: #1f6fbf;
  }
  * { margin: 0; padding: 0; box-sizing: border-box; }
  html, body { width: 1200px; height: 960px; overflow: hidden; }
  body { background: var(--stage); position: relative; font-family: "Roboto", Arial, sans-serif; }

  .card { position: absolute; width: 600px; height: 342px; overflow: hidden;
          box-shadow: 0 3px 8px rgba(0,0,0,.25); }
  .card-front { left: 314px; top: 113px; background: var(--card-front); }
  .card-back { left: 311px; top: 472px; background: var(--card-back); }

  .brand { position: absolute; display: flex; align-items: center; gap: 10px; }
  .card-front .brand { right: 38px; top: 44px; }
  .brand-dot { width: 64px; height: 64px; border-radius: 50%; background: var(--brand-blue); }
  .brand-name { font-family: "Ubuntu", Arial, sans-serif; font-weight: 500; color: var(--brand-blue);
                font-size: 42px; letter-spacing: -0.5px; line-height: 1; }

  .holder { position: absolute; left: 38px; top: 150px; }
  .holder-name { font-family: "Roboto Condensed", Arial, sans-serif; font-weight: 500;
                 font-size: 21px; color: var(--brand-blue); line-height: 1.1; }
  .holder-role { font-family: "Roboto Condensed", Arial, sans-serif; font-weight: 500;
                 font-size: 15px; color: var(--brand-yellow); margin-top: 3px; }
  .divider { position: absolute; left: 38px; right: 37px; top: 200px; height: 1.5px; background: var(--rule); }

  .contacts { position: absolute; left: 36px; top: 216px; list-style: none; }
  .contacts li { display: flex; align-items: center; gap: 8px; height: 19.3px;
                 font-size: 14px; color: var(--ink); }
  .contacts svg { width: 15px; height: 15px; flex: none; }

  .band-yellow { position: absolute; left: 0; right: 0; bottom: 12px; height: 5px; background: var(--brand-yellow); }
  .band-blue { position: absolute; left: 0; right: 0; bottom: 0; height: 12px; background: var(--brand-blue); }

  .back-lockup { position: absolute; right: 43px; top: 230px; text-align: left; }
  .back-lockup .brand-name { font-size: 40px; display: block; }
  .tagline { font-family: "Ubuntu", Arial, sans-serif; font-weight: 500; font-size: 17px; line-height: 19px; }
  .tagline-risk { color: var(--tagline-blue); margin-top: 8px; padding-left: 4px; }
  .tagline-consult { color: var(--brand-yellow); padding-left: 2px; }
</style>
</head>
<body>

<section class="card card-front">
  <div class="brand">
    <span class="brand-dot"></span>
    <span class="brand-name">NetVaultic</span>
  </div>

  <div class="holder">
    <h1 class="holder-name">TAVIN ORLOWETH</h1>
    <p class="holder-role">FOUNDER &amp; CEO</p>
  </div>
  <div class="divider"></div>

  <ul class="contacts">
    <li>
      <svg viewBox="0 0 16 16"><rect x="4" y="1" width="8" height="14" rx="1.5" fill="none" stroke="var(--icon)" stroke-width="1.6"/><circle cx="8" cy="12.6" r="0.9" fill="var(--icon)"/></svg>
      555 014 2876
    </li>
    <li>
      <svg viewBox="0 0 16 16"><rect x="1.5" y="4" width="13" height="9" fill="var(--icon)"/><path d="M1.5 4 L8 9 L14.5 4" fill="none" stroke="#fff" stroke-width="1.2"/></svg>
      tavin@netvaultic.com
    </li>
    <li>
      <svg viewBox="0 0 16 16"><circle cx="8" cy="8" r="6.5" fill="var(--icon)"/><path d="M1.5 8 H14.5 M8 1.5 C5 5 5 11 8 14.5 M8 1.5 C11 5 11 11 8 14.5" fill="none" stroke="#fff" stroke-width="1"/></svg>
      www.netvaultic.com
    </li>
    <li>
      <svg viewBox="0 0 16 16"><circle cx="8" cy="8" r="6.5" fill="var(--icon)"/></svg>
      netvaultic
    </li>
  </ul>

  <div class="band-yellow"></div>
  <div class="band-blue"></div>
</section>

<section class="card card-back">
  <div class="back-lockup">
    <span class="brand-name">NetVaultic</span>
    <p class="tagline tagline-risk">Cyber Risk Management</p>
    <p class="tagline tagline-consult">Governance &amp; Consulting</p>
  </div>
</section>

</body>
</html>
```